MRT Property - Business Cards

Looking for a business card & general letterhead, signage etc design for our new logo.

Colours:
000a20
0056a2
00b5ef
0088ce
68cef2

Fonts:
Poppins
Karla

Please keep look and feel of new brand - example in the zip package I sent.

```html
<!DOCTYPE html>
<html lang="en">
<head>
<meta charset="utf-8">
<title>MRT Property – Letterhead</title>
<link rel="stylesheet" href="https://fonts.googleapis.com/css2?family=Poppins:wght@400;600&display=swap">
<style>
  :root {
    --navy: #0e1428;
    --sky: #68cef2;
    --cyan: #00b5ef;
    --paper: #ffffff;
    --backdrop: #8c8c8c;
    --ink-light: #ffffff;
  }
  * { margin: 0; padding: 0; box-sizing: border-box; }
  html, body {
    width: 1200px; height: 686px; overflow: hidden;
    background: var(--backdrop);
    font-family: "Poppins", sans-serif;
  }
  .letterhead {
    position: absolute;
    left: 374px; top: 23px;
    width: 452px; height: 640px;
    background: var(--paper);
    box-shadow: 0 4px 14px rgba(0,0,0,0.25);
    display: flex; flex-direction: column;
  }
  .letterhead__header {
    height: 62px;
    background: var(--navy);
    border-bottom: 4px solid var(--sky);
    display: flex; align-items: center; justify-content: flex-end;
    padding-right: 28px;
  }
  .brand {
    display: flex; align-items: center; gap: 8px;
    color: var(--ink-light);
    font-weight: 600; font-size: 19px; letter-spacing: 0.5px;
  }
  .brand__dot {
    width: 14px; height: 14px; border-radius: 50%;
    background: var(--sky);
  }
  .letterhead__body { flex: 1; }
  .letterhead__footer {
    height: 70px;
    background: var(--navy);
    border-top: 4px solid var(--sky);
    display: flex; align-items: center;
    padding: 0 22px 0 18px;
    gap: 20px;
    color: var(--ink-light);
    font-size: 7.5px; line-height: 1.45;
  }
  .footer__mark {
    width: 30px; height: 30px; border-radius: 50%;
    background: var(--sky); flex: none;
  }
  .contact-list { list-style: none; }
  .contact-list li { display: flex; align-items: center; gap: 5px; }
  .icon { width: 7px; height: 7px; flex: none; }
  .address { margin-left: auto; display: flex; align-items: flex-start; gap: 6px; }
  .address .icon { width: 9px; height: 9px; margin-top: 1px; }
</style>
</head>
<body>
  <main class="letterhead">
    <header class="letterhead__header">
      <div class="brand"><span class="brand__dot"></span>MRT Property</div>
    </header>

    <section class="letterhead__body"></section>

    <footer class="letterhead__footer">
      <span class="footer__mark"></span>
      <ul class="contact-list">
        <li>
          <svg class="icon" viewBox="0 0 10 10"><path d="M2 1 L4 1 L4.6 3.2 L3.4 4 Q4.4 6 6 6.6 L6.8 5.4 L9 6 L9 8 Q9 9 8 9 Q1 8.4 1 2 Q1 1 2 1Z" fill="#68cef2"/></svg>
          +61 2 9310 4480
        </li>
        <li>
          <svg class="icon" viewBox="0 0 10 10"><g fill="none" stroke="#68cef2" stroke-width="1"><circle cx="5" cy="5" r="4"/><ellipse cx="5" cy="5" rx="1.8" ry="4"/><path d="M1 5 H9"/></g></svg>
          www.mrtproperty.com.au
        </li>
        <li>
          <svg class="icon" viewBox="0 0 10 10"><g fill="none" stroke="#68cef2" stroke-width="1"><rect x="1" y="2" width="8" height="6"/><path d="M1 2 L5 5.5 L9 2"/></g></svg>
          info@mrtproperty.com.au
        </li>
      </ul>
      <div class="address">
        <svg class="icon" viewBox="0 0 10 10"><path d="M5 0.5 A3.3 3.3 0 0 1 8.3 3.8 C8.3 6 5 9.5 5 9.5 C5 9.5 1.7 6 1.7 3.8 A3.3 3.3 0 0 1 5 0.5Z" fill="#68cef2"/><circle cx="5" cy="3.8" r="1.2" fill="#0e1428"/></svg>
        <p>Suite 4.12, Level 4<br>18 Harbourline Street<br>Rivermont NSW 2199</p>
      </div>
    </footer>
  </main>
</body>
</html>
```